Business Card Design Project

The logo I included in my order was a previous image that we've used for shirts, signs, magnets, etc. We've decided to go back to that logo, with some updates.
We need to add "Inc." after "Dunmore Roofing,"
Also, I need the logo with a transparent background so that I can use it on other projects.

The business cards will be the first item I order with the new logo. The employee's info is:
Glenn Parry
Sales Manager
484-610-3357
gparry@dunmoreroofinginc.example

Also, I want a "Find us on Chatterly" icon on the card, along with our web address, www.dunmoreroofinginc.example.

Any questions, please email or call me:
lindadunmore@mailbox.example
484-729-1186

Reason: This is the first time I've tried Pixel Forum.

My timetable changed and I need to select a design by the end of the work day, 6 hours from now.Thanks so much for all of the super designs.

Target Market(s)

Homeowners

Industry/Entity Type

Business

Font styles to use
Serif

Requirements
Must have
• Transparent background
Similar to logo in photo I sent you

```html
<!DOCTYPE html>
<html lang="en">
<head>
<meta charset="utf-8">
<title>Dunmore Roofing Inc. – Business Card</title>
<link href="https://fonts.googleapis.com/css2?family=Barlow:wght@400;500;600&family=Oswald:wght@600&family=Tinos:ital@1&display=swap" rel="stylesheet">
<style>
  :root {
    --backdrop: #3b3735;
    --card: #ffffff;
    --green: #76924a;
    --ink: #1f1f1f;
    --band-text: #ffffff;
  }
  * { margin: 0; padding: 0; box-sizing: border-box; }
  html, body { width: 1200px; height: 840px; overflow: hidden; }
  body { background: var(--backdrop); position: relative; font-family: "Barlow", Arial, sans-serif; }

  .card {
    position: absolute; left: 60px; top: 105px;
    width: 1080px; height: 630px;
    background: var(--card); overflow: hidden;
  }

  .brand { position: absolute; left: 70px; top: 100px; width: 300px; text-align: center; color: var(--ink); }
  .brand-name { font-size: 30px; font-weight: 500; line-height: 1.2; }
  .brand-phone { font-size: 26px; font-weight: 500; margin-top: 8px; }

  .person { position: absolute; left: 52px; top: 272px; }
  .person-name {
    font-family: "Oswald", "Arial Narrow", sans-serif; font-weight: 600;
    font-size: 54px; line-height: 1; color: var(--green); letter-spacing: -1px;
  }
  .person-title { font-size: 34px; color: var(--ink); margin-top: 10px; letter-spacing: 0.5px; }

  .social { position: absolute; left: 52px; top: 412px; display: flex; align-items: center; gap: 12px; }
  .social-square { width: 66px; height: 66px; background: var(--green); border-radius: 5px; }
  .social-handle { font-size: 31px; font-weight: 600; color: var(--ink); }

  .divider { position: absolute; left: 540px; top: 215px; width: 3px; height: 272px; background: var(--green); }

  .contact { position: absolute; right: 52px; top: 240px; list-style: none; text-align: right; color: var(--ink); }
  .contact li { display: flex; justify-content: flex-end; align-items: center; gap: 10px; }
  .contact svg { width: 26px; height: 26px; flex: none; fill: var(--green); }
  .contact-phone { font-size: 36px; font-weight: 500; margin-bottom: 8px; }
  .contact-line { font-size: 27px; margin-bottom: 10px; letter-spacing: 0.3px; }
  .contact-address { font-size: 27px; line-height: 1.5; margin-top: 6px; align-items: flex-start !important; letter-spacing: 0.3px; }
  .contact-address svg { margin-top: 6px; }

  .band-rule { position: absolute; left: 0; top: 512px; width: 100%; height: 3px; background: var(--green); }
  .band {
    position: absolute; left: 0; top: 521px; width: 100%; height: 109px;
    background: var(--green); color: var(--band-text);
    display: flex; align-items: center; justify-content: center;
    font-family: "Tinos", "Times New Roman", serif; font-style: italic; font-size: 44px;
    padding-bottom: 16px;
  }
</style>
</head>
<body>
  <section class="card" aria-label="Dunmore Roofing business card">
    <div class="brand">
      <div class="brand-name">Dunmore Roofing Inc.</div>
      <div class="brand-phone">610-482-7715</div>
    </div>

    <div class="person">
      <h1 class="person-name">GLENN PARRY</h1>
      <p class="person-title">Sales Manager</p>
    </div>

    <div class="social">
      <span class="social-square"></span>
      <span class="social-handle">Chatterly /dunmoreroofinginc</span>
    </div>

    <div class="divider"></div>

    <ul class="contact">
      <li class="contact-phone">484-610-3357
        <svg viewBox="0 0 24 24" aria-hidden="true"><path d="M6.6 10.8c1.4 2.8 3.8 5.1 6.6 6.6l2.2-2.2c.3-.3.7-.4 1-.2 1.1.4 2.3.6 3.6.6.6 0 1 .4 1 1V20c0 .6-.4 1-1 1C10.6 21 3 13.4 3 4c0-.6.4-1 1-1h3.5c.6 0 1 .4 1 1 0 1.3.2 2.5.6 3.6.1.3 0 .7-.2 1z"/></svg>
      </li>
      <li class="contact-line">gparry@dunmoreroofinginc.example
        <svg viewBox="0 0 24 24" aria-hidden="true"><path d="M2 5h20v14H2z M3.5 6.5 12 13l8.5-6.5" fill="var(--green)" stroke="#fff" stroke-width="1.4"/></svg>
      </li>
      <li class="contact-line">www.dunmoreroofinginc.example
        <svg viewBox="0 0 24 24" aria-hidden="true"><circle cx="12" cy="12" r="9" fill="none" stroke="var(--green)" stroke-width="2"/><path d="M3 12h18M12 3c3 3 3 15 0 18M12 3c-3 3-3 15 0 18" fill="none" stroke="var(--green)" stroke-width="1.6"/></svg>
      </li>
      <li class="contact-address"><span>348 Ridgeline Road<br>Harlow Falls, PA 18190</span>
        <svg viewBox="0 0 24 24" aria-hidden="true"><path d="M12 2a7 7 0 0 0-7 7c0 5 7 13 7 13s7-8 7-13a7 7 0 0 0-7-7zm0 9.5A2.5 2.5 0 1 1 12 6.5a2.5 2.5 0 0 1 0 5z"/></svg>
      </li>
    </ul>

    <div class="band-rule"></div>
    <div class="band">Roofing - Siding - Seemless Gutters</div>
  </section>
</body>
</html>
```